New website design and logo for FlintBoro.com to help ignite the website sales.

Hi designers,

Flintboro is a new welding brand that is selling welding equipement.

Currently I have around 5 to 10 products. The issue is that the site itself does not do that much of sales. So I have to do something about the seo etc. but that is out of scope for the design.

What is in scope is to comeup with a new logo and website look and feel that is in line with the customers.

men, non professionals, garage, home improvements, perhaps sme ( small mediul entreprice business that want to start in the welding industry.

Products are midrange prices and quality. The look and feel must breath cool stuff, sexy ( women in working cloths carrying welding gloves, other protection gear and weldels)

The wedsite is build in wordpress with the Kora theme. I am an IT guy myself withhout any creativity in me :( so if you can help me with that that would be great.

Please have a quick look at flintboro.com

Best regards,
Joris

Target Market(s)

non professional welders that do metal work in there garage

Coding

Coded - Design and coding required

Number of Pages Required

3 page

Font styles to use
Sans Serif

Colors
0355a3
ffc214

Requirements
Must have
• I would like to see a new homepage and product page design together with a new logo.
Nice to have
• shop design

```html
<!DOCTYPE html>
<html lang="nl">
<head>
<meta charset="utf-8">
<title>Flintboro – Welding equipment</title>
<link href="https://fonts.googleapis.com/css2?family=Roboto:wght@400;500;700;900&display=swap" rel="stylesheet">
<style>
:root{
  --blue:#2178d4;
  --blue-dark:#0355a3;
  --yellow:#ffb400;
  --ink:#111111;
  --muted:#555555;
  --line:#e2e2e2;
  --field:#ffffff;
  --page:#ffffff;
  --footer:#000000;
}
*{box-sizing:border-box;margin:0;padding:0}
html,body{width:1200px;height:3012px;overflow:hidden}
body{position:relative;background:var(--page);font-family:'Roboto',sans-serif;color:var(--ink)}
.abs{position:absolute}

/* header */
.site-header{position:absolute;left:0;top:0;width:1200px;height:105px;background:#fff}
.brand{position:absolute;display:flex;align-items:center;gap:10px}
.brand-dot{width:44px;height:44px;border-radius:50%;background:var(--yellow)}
.brand-name{font-weight:700;font-size:22px;color:var(--blue-dark)}
.search{left:488px;top:21px;width:282px;height:34px;border:1px solid #d6d6d6;font-size:14px;color:#777;padding:9px 13px}
.search svg{position:absolute;right:12px;top:10px}
.call{left:850px;top:28px;font-size:15px;font-weight:500;display:flex;align-items:center;gap:8px}
.call .lbl{color:var(--blue);font-weight:400}
.nav a{position:absolute;top:72px;font-size:14px;font-weight:500;color:var(--ink);text-decoration:none}
.nav a.active{color:var(--yellow)}
.cart{left:1008px;top:74px;display:flex;align-items:center;gap:10px;font-size:12px;font-weight:500}

/* hero */
.hero{left:0;top:105px;width:1200px;height:580px;background:radial-gradient(ellipse at 80% 45%,#f0a840 0%,#8a5a25 25%,#3a2e25 55%,#1f2226 100%)}
.hero-box{left:97px;top:309px;width:577px;height:139px;background:var(--blue);border-left:5px solid var(--yellow);padding:28px 16px 0 34px;color:#fff}
.hero-box h1{font-size:30px;font-weight:700;line-height:32px;white-space:nowrap;letter-spacing:-.2px}
.hero-box p{font-size:26px;line-height:27px}

.ship{left:0;width:1200px;text-align:center}
.ship-ghost{top:718px;font-size:38px;font-weight:700;color:#e6e6e6}
.ship-main{top:755px;font-size:19px;font-weight:500}
.rule{left:97px;top:819px;width:1005px;height:1px;background:var(--line)}

/* products */
.section-title{font-size:43px;font-weight:900;letter-spacing:.5px;text-transform:uppercase}
.intro{font-size:14px;line-height:21px;color:var(--muted);width:450px}
.tabs span{position:absolute;top:982px;font-size:14px;font-weight:500}
.tab-line{left:650px;top:1014px;width:452px;height:3px;background:#e8e8e8}
.tab-line i{position:absolute;left:0;top:0;width:176px;height:3px;background:var(--blue)}
.card{position:absolute;top:1053px;width:244px;height:365px;background:#fff;box-shadow:0 2px 14px rgba(0,0,0,.09);text-align:center}
.card .shot{position:absolute;left:10px;top:23px;width:224px;height:228px}
.card h3{position:absolute;left:0;right:0;top:270px;font-size:19px;font-weight:500;line-height:21px}
.card .price{position:absolute;left:0;right:0;font-size:12px;color:var(--blue)}
.card .buy{position:absolute;left:100px;top:343px;width:45px;height:45px;border-radius:50%;background:var(--blue);display:flex;align-items:center;justify-content:center}
.prev{left:97px;top:1207px;width:46px;height:46px;border-radius:50%;background:#fff;box-shadow:0 2px 10px rgba(0,0,0,.12);display:flex;align-items:center;justify-content:center}

/* about */
.about-photo{left:0;top:1555px;width:1200px;height:580px;background:linear-gradient(120deg,#6e5232 0%,#a8835a 25%,#9aa0a6 50%,#5d6066 75%,#8a5a2a 100%)}
.about-box{left:526px;top:1670px;width:576px;height:350px;background:var(--blue);border-left:5px solid var(--yellow);padding:44px 37px 0 37px;color:#fff}
.about-box h2{font-size:42px;font-weight:900}
.about-box p{margin-top:14px;font-size:14px;line-height:24px;text-align:justify}
.btn{display:inline-block;background:var(--yellow);color:#fff;font-weight:500;font-size:15px;text-align:center}
.about-box .btn{margin-top:26px;width:148px;height:38px;line-height:38px}

/* contact */
.contact-item{position:absolute;left:97px;display:flex;gap:13px}
.contact-item .ic{width:42px;height:42px;border-radius:50%;border:2px solid var(--blue);display:flex;align-items:center;justify-content:center;flex:none}
.contact-item b{display:block;color:var(--blue);font-weight:500;font-size:14px;line-height:21px}
.contact-item span{font-size:14px;line-height:21px;color:#333;display:block;width:260px}
.field{position:absolute;background:var(--field);box-shadow:0 1px 8px rgba(0,0,0,.08);font-size:13px;color:#777;padding:13px 15px}
.submit{left:601px;top:2489px;width:148px;height:38px;line-height:38px}

/* footer */
.site-footer{left:0;top:2669px;width:1200px;height:343px;background:var(--footer);color:#fff}
.foot-links a{position:absolute;top:202px;font-size:15px;font-weight:500;color:#fff;text-decoration:none;transform:translateX(-50%)}
.socials{left:523px;top:276px;display:flex;gap:26px}
.socials i{width:9px;height:9px;border-radius:50%;background:#fff;display:block}
.copy{left:0;width:1200px;top:306px;text-align:center;font-size:13px;color:#fff}
</style>
</head>
<body>

<header class="site-header">
  <div class="brand" style="left:99px;top:32px"><span class="brand-dot"></span><span class="brand-name">Flintboro</span></div>
  <div class="abs search">Search
    <svg width="13" height="13" viewBox="0 0 13 13"><circle cx="5.5" cy="5.5" r="4.2" fill="none" stroke="#111" stroke-width="1.8"/><line x1="8.6" y1="8.6" x2="12" y2="12" stroke="#111" stroke-width="2"/></svg>
  </div>
  <div class="abs call">
    <svg width="14" height="14" viewBox="0 0 24 24"><path fill="#2178d4" d="M6.6 10.8a15 15 0 0 0 6.6 6.6l2.2-2.2a1 1 0 0 1 1-.25 11.4 11.4 0 0 0 3.6.57 1 1 0 0 1 1 1V20a1 1 0 0 1-1 1A17 17 0 0 1 3 4a1 1 0 0 1 1-1h3.5a1 1 0 0 1 1 1c0 1.25.2 2.45.57 3.6a1 1 0 0 1-.25 1z"/></svg>
    <span><span class="lbl">Call Us</span> : +31(0)201234567</span>
  </div>
  <nav class="nav">
    <a class="active" style="left:489px">Home</a>
    <a style="left:593px">Products</a>
    <a style="left:715px">Winkelmand</a>
    <a style="left:857px">Mijn account</a>
  </nav>
  <div class="abs cart">
    <svg width="16" height="14" viewBox="0 0 24 20"><path d="M0 1h4l3 11h12l3-8H6.5" fill="none" stroke="#2178d4" stroke-width="2.2"/><circle cx="8.5" cy="17" r="2" fill="#2178d4"/><circle cx="17.5" cy="17" r="2" fill="#2178d4"/></svg>
    <span>Add To Cart</span>
  </div>
</header>

<div class="abs hero" role="img" aria-label="Close-up of a metal cutting machine throwing bright orange sparks"></div>
<div class="abs hero-box">
  <h1>Eenvoudig staal en aluminium lassen</h1>
  <p>Krijg fantastisch resultaat met gereedschap dat werkt</p>
</div>

<div class="abs ship ship-ghost">Gratis versturen vanaf € 30,00</div>
<div class="abs ship ship-main">Gratis versturen vanaf € 30,00</div>
<div class="abs rule"></div>

<section>
  <h2 class="abs section-title" style="left:97px;top:922px">Our Products</h2>
  <p class="abs intro" style="left:97px;top:978px">Lorem ipsum dolor sit amet, consectetur adipiscing elit, sed do eiusmod tempor incididunt ut labore et dolore magna aliqua.</p>
  <div class="tabs"><span style="left:651px">Handschoenen</span><span style="left:896px">Mig</span></div>
  <div class="abs tab-line"><i></i></div>

  <div class="abs prev"><svg width="10" height="12" viewBox="0 0 10 12"><path d="M7 1 2 6l5 5" fill="none" stroke="#555" stroke-width="1.5"/></svg></div>

  <article class="card" style="left:188px">
    <div class="shot" role="img" aria-label="Red and black MIG welding machine" style="background:linear-gradient(160deg,#d9483a,#3a2a28)"></div>
    <h3>MIG-250P</h3><div class="price" style="top:298px">€845,00 €795,00</div>
    <div class="buy"><svg width="22" height="20" viewBox="0 0 24 20"><path d="M1 2h4l3 10h11l3-7H6" fill="none" stroke="#fff" stroke-width="1.6"/><circle cx="9" cy="17" r="1.6" fill="#fff"/><circle cx="18" cy="17" r="1.6" fill="#fff"/></svg></div>
  </article>
  <article class="card" style="left:446px">
    <div class="shot" role="img" aria-label="Blue and silver MIG welding machine" style="background:linear-gradient(160deg,#c7ccd2,#3f76c4)"></div>
    <h3>MIG-2500</h3><div class="price" style="top:298px">€745,00</div>
    <div class="buy"><svg width="22" height="20" viewBox="0 0 24 20"><path d="M1 2h4l3 10h11l3-7H6" fill="none" stroke="#fff" stroke-width="1.6"/><circle cx="9" cy="17" r="1.6" fill="#fff"/><circle cx="18" cy="17" r="1.6" fill="#fff"/></svg></div>
  </article>
  <article class="card" style="left:704px">
    <div class="shot" role="img" aria-label="Black welding helmet with purple visor" style="background:linear-gradient(160deg,#5a5a5a,#1c1c1c)"></div>
    <h3>Welding helmet 180<br>degrees view</h3><div class="price" style="top:318px">€845,00 €795,00</div>
    <div class="buy"><svg width="22" height="20" viewBox="0 0 24 20"><path d="M1 2h4l3 10h11l3-7H6" fill="none" stroke="#fff" stroke-width="1.6"/><circle cx="9" cy="17" r="1.6" fill="#fff"/><circle cx="18" cy="17" r="1.6" fill="#fff"/></svg></div>
  </article>
  <article class="card" style="left:961px">
    <div class="shot" role="img" aria-label="Black welding helmet with large purple visor" style="background:linear-gradient(160deg,#5a5a5a,#1c1c1c)"></div>
    <h3>Welding helmet large view</h3><div class="price" style="top:298px">€89,00</div>
    <div class="buy"><svg width="22" height="20" viewBox="0 0 24 20"><path d="M1 2h4l3 10h11l3-7H6" fill="none" stroke="#fff" stroke-width="1.6"/><circle cx="9" cy="17" r="1.6" fill="#fff"/><circle cx="18" cy="17" r="1.6" fill="#fff"/></svg></div>
  </article>
</section>

<section>
  <div class="abs about-photo" role="img" aria-label="Plasma cutter piercing a steel plate with sparks flying"></div>
  <div class="abs about-box">
    <h2>ABOUT US</h2>
    <p>Lorem ipsum dolor sit amet, consectetur adipiscing elit, sed do eiusmod tempor incididunt ut labore et dolore magna aliqua. Ut enim ad minim veniam, quis nostrud exercitation ullamco laboris nisi ut aliquip ex ea commodo consequat. Duis aute irure dolor in reprehenderit in voluptate velit esse cillum dolore eu fugiat nulla pariatur.</p>
    <span class="btn">Read More</span>
  </div>
</section>

<section>
  <h2 class="abs section-title" style="left:97px;top:2240px">Contact Us</h2>
  <p class="abs intro" style="left:97px;top:2295px">Lorem ipsum dolor sit amet, consectetur adipiscing elit, sed do eiusmod tempor incididunt ut labore et dolore magna aliqua.</p>

  <div class="contact-item" style="top:2367px">
    <div class="ic"><svg width="16" height="16" viewBox="0 0 24 24"><path fill="#2178d4" d="M6.6 10.8a15 15 0 0 0 6.6 6.6l2.2-2.2a1 1 0 0 1 1-.25 11.4 11.4 0 0 0 3.6.57 1 1 0 0 1 1 1V20a1 1 0 0 1-1 1A17 17 0 0 1 3 4a1 1 0 0 1 1-1h3.5a1 1 0 0 1 1 1c0 1.25.2 2.45.57 3.6a1 1 0 0 1-.25 1z"/></svg></div>
    <div><b>Call Us:</b><span>+31(0)201234567</span></div>
  </div>
  <div class="contact-item" style="top:2433px">
    <div class="ic"><svg width="18" height="14" viewBox="0 0 18 14"><rect width="18" height="14" rx="2" fill="#2178d4"/><path d="M1 2l8 6 8-6" fill="none" stroke="#fff" stroke-width="1.5"/></svg></div>
    <div><b>Email Us:</b><span>hello@flintboro.com</span></div>
  </div>
  <div class="contact-item" style="top:2498px">
    <div class="ic"><svg width="12" height="17" viewBox="0 0 12 17"><path fill="#2178d4" d="M6 0a6 6 0 0 1 6 6c0 4.5-6 11-6 11S0 10.5 0 6a6 6 0 0 1 6-6z"/><circle cx="6" cy="6" r="2.2" fill="#fff"/></svg></div>
    <div><b>Address:</b><span>Lorem ipsum dolor sit amet, consectetur adipiscing elit, sed do</span></div>
  </div>

  <div class="field" style="left:601px;top:2261px;width:244px;height:39px">Name</div>
  <div class="field" style="left:856px;top:2261px;width:244px;height:39px">Email</div>
  <div class="field" style="left:601px;top:2314px;width:244px;height:39px">Phone Number</div>
  <div class="field" style="left:856px;top:2314px;width:244px;height:39px">Company Name</div>
  <div class="field" style="left:601px;top:2366px;width:501px;height:108px">Message</div>
  <span class="abs btn submit">Submit</span>
</section>

<footer class="abs site-footer">
  <div class="brand" style="left:527px;top:104px"><span class="brand-dot"></span><span class="brand-name" style="color:#fff">Flintboro</span></div>
  <nav class="foot-links">
    <a style="left:475px">Customer care</a>
    <a style="left:623px">Informatie</a>
    <a style="left:745px">Bronnen</a>
  </nav>
  <div class="abs socials"><i></i><i></i><i></i><i></i><i></i></div>
  <div class="abs copy">Copyrights © 2021, The Company Name. All rights reserved.</div>
</footer>

</body>
</html>
```